4th Generation Family Business Needs a New Card Design!

We are a family owned 4th Generation company. We are based in the Sydney, Australia area and we are desperately in need of a more modern and classy card. We are monumental masons who design, supply & erect lasting memorials throughout cemeteries in Sydney. Our customers are normally in a period of grieving. I have attached logo files that will need to be implemented on the card. Company was established 1935. Australian Owned and Operated. Card needs to be designed to PIXO.com specification.

Target Market(s)

Our target market is based upon people that a grieving for family members that have passed away. We also deal with alot of companies that own and operate cemeteries.

Industry/Entity Type

Business

Contact Information for Business Card

Simon Harcourt, Operations Manager, 0417293086, simon@harcourtmemorials.com.au
Lewis Harcourt, Director, 0491630572, lewis@harcourtmemorials.com.au
Phone # 02 9561 3048
Website: www.harcourtmemorials.com.au
Address: Suite 17, 8 Palfrey Lane, West Carlow, Sydney NSW 2156

Font styles to use
Serif
Decorative
Script

Requirements
Must have
• Would like to see the logo nicely implemented with a modern design. Embossed lettering would be a nice additive.

```html
<!DOCTYPE html>
<html lang="en">
<head>
<meta charset="utf-8">
<title>Harcourt Memorials – Business Card</title>
<link href="https://fonts.googleapis.com/css2?family=Merriweather:ital,wght@0,400;0,700;1,400&display=swap" rel="stylesheet">
<style>
  :root {
    --backdrop: #2b2d31;
    --card-white: #ffffff;
    --card-gold: #ecc04a;
    --card-gold-deep: #e6b63b;
    --card-slate: #3a3e46;
    --ink: #1b1b1b;
    --ink-soft: #3a3328;
    --emboss-light: rgba(255, 255, 255, 0.55);
    --emboss-dark: rgba(90, 64, 10, 0.45);
  }
  html, body {
    margin: 0;
    padding: 0;
    width: 1200px;
    height: 900px;
    overflow: hidden;
    background: var(--backdrop);
    font-family: "Merriweather", Georgia, serif;
  }
  .canvas {
    position: relative;
    width: 1200px;
    height: 900px;
  }
  .card {
    position: absolute;
    left: 320px;
    width: 560px;
    height: 320px;
    box-shadow: 0 12px 30px rgba(0, 0, 0, 0.45);
    overflow: hidden;
  }
  .card-front { top: 80px; display: flex; }
  .card-back {
    top: 500px;
    background: var(--card-slate);
    display: flex;
    align-items: center;
    justify-content: center;
  }

  /* Front: brand panel */
  .brand-panel {
    width: 208px;
    background: var(--card-white);
    position: relative;
  }
  .brand-name {
    position: absolute;
    top: 92px;
    left: 0;
    right: 0;
    text-align: center;
    color: var(--ink);
    font-weight: 400;
    font-size: 21px;
    line-height: 1.25;
    letter-spacing: 2px;
    text-transform: uppercase;
  }
  .brand-name .brand-sub {
    display: block;
    font-size: 13px;
    letter-spacing: 3px;
  }
  .web-address {
    position: absolute;
    left: 0;
    right: 0;
    bottom: 26px;
    text-align: center;
    font-size: 10px;
    color: var(--ink);
  }

  /* Front: details panel */
  .details-panel {
    flex: 1;
    background: linear-gradient(135deg, var(--card-gold), var(--card-gold-deep));
    position: relative;
    padding: 26px 24px;
    box-sizing: border-box;
  }
  .holder-name {
    margin: 0;
    font-size: 22px;
    font-weight: 400;
    font-style: italic;
    color: var(--card-gold);
    text-shadow: -1px -1px 0 var(--emboss-light), 1px 1px 1px var(--emboss-dark);
  }
  .holder-role {
    margin: 4px 0 0;
    font-size: 12.5px;
    color: var(--card-gold);
    text-shadow: -1px -1px 0 var(--emboss-light), 1px 1px 1px var(--emboss-dark);
  }
  .contact-block {
    position: absolute;
    left: 24px;
    bottom: 24px;
    font-size: 11px;
    line-height: 1.7;
    color: var(--ink-soft);
    font-weight: 700;
  }
  .contact-block p { margin: 0; }

  /* Back */
  .back-brand {
    text-align: center;
    color: var(--ink);
    font-weight: 400;
    font-size: 34px;
    line-height: 1.25;
    letter-spacing: 3px;
    text-transform: uppercase;
  }
  .back-brand .brand-sub {
    display: block;
    font-size: 19px;
    letter-spacing: 5px;
  }
</style>
</head>
<body>
  <main class="canvas">
    <section class="card card-front" aria-label="Business card front">
      <div class="brand-panel">
        <div class="brand-name">Harcourt<span class="brand-sub">Memorials</span></div>
        <div class="web-address">www.harcourtmemorials.com.au</div>
      </div>
      <div class="details-panel">
        <h1 class="holder-name">Simon Harcourt</h1>
        <p class="holder-role">Operation Manager (0417293086)</p>
        <div class="contact-block">
          <p>Contact:</p>
          <p>02 9561 3048</p>
          <p>simon@harcourtmemorials.com.au</p>
          <p>Suite 17, 8 Palfrey Lane, West Carlow, Sydney NSW 2156</p>
        </div>
      </div>
    </section>

    <section class="card card-back" aria-label="Business card back">
      <div class="back-brand">Harcourt<span class="brand-sub">Memorials</span></div>
    </section>
  </main>
</body>
</html>
```